Copper Lantern

Need a business card for our restaurant. Restaurant and Bar in the mountains of North Idaho. Rustic looking card

rustic design, wood and metal looking, primarily neutral colors

• Name, address, phone number, website, email address

```html
<!DOCTYPE html>
<html lang="en">
<head>
<meta charset="utf-8">
<title>Copper Lantern – Business Card</title>
<link rel="stylesheet" href="https://fonts.googleapis.com/css2?family=Montserrat:wght@400;700&display=swap">
<style>
  :root {
    --page-bg: #2a2a2a;
    --card-black: #141414;
    --card-back: #1c1c1c;
    --ink-white: #f2f2f2;
    --ink-soft: #d8d8d8;
    --pattern-light: #8a8a8a;
    --pattern-dark: #161616;
  }
  * { box-sizing: border-box; margin: 0; padding: 0; }
  html, body {
    width: 1200px; height: 875px; overflow: hidden;
    background: var(--page-bg);
    font-family: "Montserrat", sans-serif;
  }
  .sheet {
    width: 1200px; height: 875px;
    display: flex; align-items: center; justify-content: center; gap: 48px;
  }
  .card {
    width: 540px; height: 310px;
    border-radius: 22px;
    position: relative; overflow: hidden;
    box-shadow: 0 18px 40px rgba(0,0,0,.45);
  }
  .card-front { background: var(--card-black); }
  .front-pattern {
    position: absolute; inset: 0;
    background: linear-gradient(110deg, var(--pattern-light) 0%, #3a3a3a 30%, var(--pattern-dark) 60%, var(--card-black) 100%);
    opacity: .55;
  }
  .front-mark {
    position: absolute; left: 340px; top: 140px;
    color: var(--ink-white);
    font-weight: 700; font-size: 15px; letter-spacing: .04em;
  }
  .card-back {
    background: var(--card-back);
    display: flex; align-items: center;
    padding: 0 40px 0 60px;
  }
  .brand {
    display: flex; align-items: center; gap: 12px;
    width: 220px;
  }
  .brand-dot {
    width: 26px; height: 26px; border-radius: 50%;
    border: 2px solid var(--ink-white); flex: none;
  }
  .brand-name {
    color: var(--ink-white); font-weight: 700; font-size: 17px;
    text-transform: uppercase; letter-spacing: .06em; line-height: 1.25;
  }
  .divider {
    width: 1px; height: 150px; background: var(--ink-soft);
    margin: 0 22px 0 16px;
  }
  .details { color: var(--ink-white); }
  .person-name { font-weight: 700; font-size: 20px; }
  .person-role { font-size: 12px; color: var(--ink-soft); margin-bottom: 12px; }
  .address { font-size: 12px; line-height: 1.35; margin-bottom: 10px; }
  .contact-list { list-style: none; font-size: 12px; }
  .contact-list li { display: flex; align-items: center; gap: 8px; line-height: 1.6; }
  .contact-list svg { width: 11px; height: 11px; fill: var(--ink-white); flex: none; }
</style>
</head>
<body>
<main class="sheet">
  <section class="card card-front">
    <div class="front-pattern" role="img" aria-label="Repeating brand symbol pattern in glossy black and silver"></div>
    <span class="front-mark">Copper Lantern</span>
  </section>

  <section class="card card-back">
    <div class="brand">
      <span class="brand-dot"></span>
      <span class="brand-name">Copper Lantern</span>
    </div>
    <div class="divider"></div>
    <div class="details">
      <p class="person-name">Daniel Reeve</p>
      <p class="person-role">Managing Director</p>
      <p class="address">48 Ridge Road,<br>Cedar Hollow, USA</p>
      <ul class="contact-list">
        <li><svg viewBox="0 0 12 12"><path d="M2 1h2.5l1 3-1.5 1a7 7 0 0 0 3 3l1-1.5 3 1V11C6 11 1 6 1 2z"/></svg>(08) 4310 2286</li>
        <li><svg viewBox="0 0 12 12"><path d="M0 2h12v8H0zM1 3v.4l5 3.4 5-3.4V3z"/></svg>hello@copperlantern.com</li>
        <li><svg viewBox="0 0 12 12"><circle cx="6" cy="6" r="5.5"/></svg>www.copperlantern.com</li>
      </ul>
    </div>
  </section>
</main>
</body>
</html>
```